Flyer Vacation Gift Certificate

I need to create a beautiful flyer 8.5 x 11 PDF format flyer design. <br/><br/>Instructions:<br/>The flyer will really be a gift voucher for a las vegas vacation getaway. So must have a Las Vegas Theme exciting fun<br/><br/>The voucher should have two modules that will be editable. <br/>Must have a "Compliments Of" area and also must have an "Exclusively For" area<br/><br/>Keep in mind that this flyer will be printed so keep that in mind :)<br/><br/>Here the is the content for the vacation voucher:<br/><br/>There is no doubt that Las Vegas is one of the hottest travel destinations around the world. In fact, some people would even go as far as<br/>saying that perhaps it is THE hottest place to visit. Enjoy up to 4 nights of resort/casino accommodations in exciting Las Vegas, NV. Millions of people travel to this exciting city each year to enjoy its thrills. Thanks to the business you received this certificate from, now you can enjoy exciting Las Vegas, NV too!<br/><br/>Features:<br/>*Travel 7 Days A Week<br/>*Stay Your Choice Of Nights (1-4 Nights)<br/>*Good For Two Adults & Two Children<br/>*Pay Just The Taxes & Fees<br/>*Multiple Travel Date Requests Allowed<br/>*Fully Transferable To Another Person<br/>*Just A 30 Days Advance Notice Required<br/>*You Will Have 12 Months To Complete Travel After Redemption<br/><br/>HOW CAN WE DO THIS?<br/><br/>We contract with the world leading hotel chains and resorts to help them fill their otherwise empty rooms.<br/><br/>We help fill empty rooms which the hotels, resorts and cruise lines turn into additional revenue from other areas of their property and future bookings.<br/><br/>Hotels rarely experience full occupancy, yet they remain open, providing rooms and services at fixed costs. So when hotels give out their rooms by partnering with marketing companies like us, they might miss out on the room fee, but they already didn't have that in the first place, at least now they have the opportunity to gain a customer for their in-house restaurants, room service, their casinos, an extra day stay, future bookings, etc.<br/><br/>VIEW ALL THE DETAILS OF THIS SPECIAL OFFER AND REDEEM ONLINE AT <br/>WWW.QOTAVERNIX.COM<br/><br/>Certificate ID # 47261-38157<br/>Expires 02/29/2020<br/><br/><br/>*terms and conditions apply see website for details<br/><br/>KEEP IN MIND THE EXAMPLES I AM UPLOADING ARE SIMPLY TO SHOW YOU THAT THEY CONTAIN THE "COMPLIMENTS OF" AND "EXCLUSIVELY FOR" ELEMENTS. THESE MUST BE INCLUDED IN NEW DESIGN. PLEASE ONLY USE THE CONTENT I PROVIDED IN BRIEF, DONT USE CONTENT FROM EXAMPLES.

Target Market(s)

CONSUMERS THAT HAVE BEEN REWARDED WITH A VACATION CERTIFICATE FOR DOING BUSINESS WITH A COMPANY.

COMPANIES USE THESE AS MARKETING INCENTIVES TO ATTRACT MORE CUSTOMERS AND TO REWARD LOYALTY, ETC.

Industry/Entity Type

Travel Industry

Colors

Designer to choose colors to be used in the design.

Requirements
Must have
• I need to create a beautiful flyer 8.5 x 11 PDF format flyer design.
• Instructions:
• The flyer will really be a gift voucher for a las vegas vacation getaway. So must have a Las Vegas Theme exciting fun
• The voucher should have two modules that will be editable.
• Must have a "Compliments Of" area and also must have an "Exclusively For" area
• Keep in mind that this flyer will be printed so keep that in mind :)
• Here the is the content for the vacation voucher:
• There is no doubt that Las Vegas is one of the hottest travel destinations around the world. In fact, some people would even go as far as
• saying that perhaps it is THE hottest place to visit. Enjoy up to 4 nights of resort/casino accommodations in exciting Las Vegas, NV. Millions of people travel to this exciting city each year to enjoy its thrills. Thanks to the business you received this certificate from, now you can enjoy exciting Las Vegas, NV too!
• Features:
• *Travel 7 Days A Week
• *Stay Your Choice Of Nights (1-4 Nights)
• *Good For Two Adults & Two Children
• *Pay Just The Taxes & Fees
• *Multiple Travel Date Requests Allowed
• *Fully Transferable To Another Person
• *Just A 30 Days Advance Notice Required
• *You Will Have 12 Months To Complete Travel After Redemption
• HOW CAN WE DO THIS?
• We contract with the world leading hotel chains and resorts to help them fill their otherwise empty rooms.
• We help fill empty rooms which the hotels, resorts and cruise lines turn into additional revenue from other areas of their property and future bookings.
• Hotels rarely experience full occupancy, yet they remain open, providing rooms and services at fixed costs. So when hotels give out their rooms by partnering with marketing companies like us, they might miss out on the room fee, but they already didn't have that in the first place, at least now they have the opportunity to gain a customer for their in-house restaurants, room service, their casinos, an extra day stay, future bookings, etc.
• VIEW ALL THE DETAILS OF THIS SPECIAL OFFER AND REDEEM ONLINE AT
• WWW.QOTAVERNIX.COM
• Certificate ID # 47261-38157
• Expires 02/29/2020
• *terms and conditions apply see website for details
• KEEP IN MIND THE EXAMPLES I AM UPLOADING ARE SIMPLY TO SHOW YOU THAT THEY CONTAIN THE "COMPLIMENTS OF" AND "EXCLUSIVELY FOR" ELEMENTS. THESE MUST BE INCLUDED IN NEW DESIGN. PLEASE ONLY USE THE CONTENT I PROVIDED IN BRIEF, DONT USE CONTENT FROM EXAMPLES.
Nice to have
• EXCITING LAS VEGAS IMAGES THAT MAKE SOMEONE WANT TO GO THERE

```html
<!DOCTYPE html>
<html lang="en">
<head>
<meta charset="utf-8">
<title>Las Vegas Vacation Gift Certificate</title>
<link rel="stylesheet" href="https://fonts.googleapis.com/css2?family=Poppins:wght@400;500;600;700&family=Bungee+Inline&display=swap">
<style>
  :root {
    --page: #e6e6e6;
    --red: #e8202a;
    --red-deep: #c8141e;
    --maroon: #5a0a0e;
    --black: #0d0607;
    --yellow: #ffe81a;
    --white: #ffffff;
  }
  * { box-sizing: border-box; margin: 0; padding: 0; }
  html, body { width: 1200px; height: 1000px; overflow: hidden; }
  body { background: var(--page); font-family: 'Poppins', sans-serif; position: relative; }

  .flyer {
    position: absolute; left: 260px; top: 20px;
    width: 679px; height: 960px; overflow: hidden;
    background: var(--black);
    box-shadow: 0 4px 14px rgba(0,0,0,.25);
  }

  .hero-photo {
    position: absolute; left: 0; top: 0; width: 679px; height: 484px;
    background:
      radial-gradient(ellipse at 80% 75%, #ffb23a 0%, rgba(255,140,40,.6) 22%, transparent 48%),
      radial-gradient(ellipse at 30% 55%, #3d3a40 0%, rgba(60,55,60,.7) 25%, transparent 50%),
      linear-gradient(135deg, #b52a3a 0%, #8d3fa8 35%, #d0506a 60%, #c77a3a 100%);
  }

  .title {
    position: absolute; left: 362px; top: 30px;
    font-family: 'Bungee Inline', sans-serif; font-size: 46px; line-height: 1;
    color: var(--red); -webkit-text-stroke: 1.5px var(--white);
    transform: scaleY(1.35); transform-origin: left top;
    letter-spacing: -1px;
  }

  .hero-strip {
    position: absolute; left: 0; top: 458px; width: 679px; height: 26px;
    background: var(--red-deep);
  }

  .recipient-panel {
    position: absolute; top: 276px; width: 229px; height: 197px;
    background: var(--red);
    clip-path: polygon(0 0, 100% 70%, 100% 100%, 0 100%);
  }
  .recipient-panel.exclusive { left: 32px; }
  .recipient-panel.compliments { left: 272px; }
  .recipient-panel svg { position: absolute; }
  .panel-label {
    position: absolute; left: 10px; top: 150px;
    font-weight: 600; font-size: 13.5px; color: var(--white); line-height: 1;
  }
  .panel-name {
    position: absolute; left: 10px; top: 170px;
    font-weight: 700; font-size: 18.5px; color: var(--yellow); line-height: 1;
  }

  .body-area {
    position: absolute; left: 0; top: 484px; width: 679px; height: 421px;
    background: linear-gradient(180deg, var(--maroon) 0%, #2a0709 45%, var(--black) 100%);
  }

  .intro {
    position: absolute; left: 32px; top: 503px; width: 292px;
    font-weight: 500; font-size: 13.5px; line-height: 19.5px; color: var(--white);
  }

  .features-tab {
    position: absolute; left: 33px; top: 666px; width: 164px; height: 27px;
    background: var(--red);
    clip-path: polygon(0 0, 86% 0, 100% 100%, 0 100%);
    font-weight: 600; font-size: 13.5px; line-height: 27px; color: var(--white);
    padding-left: 22px;
  }
  .features-box {
    position: absolute; left: 33px; top: 693px; width: 268px; height: 196px;
    border: 2px solid var(--red); background: var(--black);
    padding: 6px 6px 0 6px;
  }
  .features-list { list-style: none; }
  .features-list li {
    position: relative; padding-left: 25px;
    font-size: 11.2px; line-height: 15.5px; color: var(--white);
    margin-bottom: 6px;
  }
  .features-list li svg { position: absolute; left: 0; top: 0; }

  .how-title {
    position: absolute; left: 356px; top: 504px;
    font-weight: 600; font-size: 15.5px; color: var(--white);
  }
  .how-item {
    position: absolute; left: 356px; width: 296px;
    padding-left: 32px;
    font-size: 10.9px; line-height: 15.6px; color: #f1e6e6;
  }
  .how-item svg { position: absolute; left: 0; top: 0; }
  .how-item.contract { top: 542px; }
  .how-item.revenue { top: 599px; }
  .how-item.occupancy { top: 673px; }

  .divider {
    position: absolute; left: 356px; top: 837px; width: 260px; height: 2px;
    background: var(--red);
  }
  .certificate-meta {
    position: absolute; left: 356px; top: 849px;
    font-size: 10.3px; line-height: 16px; color: var(--white);
  }

  .redeem-footer {
    position: absolute; left: 0; top: 905px; width: 679px; height: 55px;
    background: var(--red);
    font-weight: 600; font-size: 13.3px; line-height: 55px; color: var(--yellow);
    padding-left: 31px; letter-spacing: -0.1px;
  }
</style>
</head>
<body>
<main class="flyer">
  <div class="hero-photo" role="img" aria-label="Photo collage of an elegant couple in evening wear beside a roulette wheel, in front of the neon Las Vegas skyline and casino resorts"></div>
  <h1 class="title">LAS VEGAS</h1>
  <div class="hero-strip"></div>

  <section class="recipient-panel exclusive">
    <svg width="66" height="104" viewBox="0 0 66 104" style="left:12px;top:30px" fill="none" stroke="var(--yellow)" stroke-width="2.6" stroke-linejoin="round">
      <ellipse cx="33" cy="30" rx="16" ry="20"/>
      <path d="M17 24 Q20 8 33 8 Q46 8 49 24"/>
      <path d="M26 50 L26 58 L33 64 L40 58 L40 50"/>
      <path d="M3 102 V78 Q3 62 20 58 L33 64 L46 58 Q63 62 63 78 V102 Z"/>
      <path d="M33 64 L29 70 L33 96 L37 70 Z"/>
      <path d="M14 80 V102 M52 80 V102"/>
    </svg>
    <div class="panel-label">EXCLUSIVELY FOR:</div>
    <div class="panel-name">CUSTOMER NAME</div>
  </section>

  <section class="recipient-panel compliments">
    <svg width="74" height="86" viewBox="0 0 74 86" style="left:12px;top:48px" fill="none" stroke="var(--yellow)" stroke-width="2.4" stroke-linejoin="round">
      <rect x="2" y="4" width="54" height="78" rx="3"/>
      <circle cx="22" cy="22" r="6"/>
      <path d="M12 40 Q12 30 22 30 Q32 30 32 40 Z"/>
      <path d="M10 50 H46 M10 57 H46 M10 64 H46 M10 71 H40"/>
      <circle cx="56" cy="24" r="15" fill="var(--red)"/>
      <path d="M56 16 L58.5 21.5 L64 22 L60 26 L61 31.5 L56 28.5 L51 31.5 L52 26 L48 22 L53.5 21.5 Z"/>
      <path d="M50 38 L48 56 L53 52 L56 57 L57 40"/>
    </svg>
    <div class="panel-label">COMPLIMENTS OF:</div>
    <div class="panel-name">CUSTOMER NAME</div>
  </section>

  <div class="body-area"></div>

  <p class="intro">Enjoy up to 4 nights of resort/casino accommodations in exciting Las Vegas, NV. Millions of people travel to this exciting city each year to enjoy its thrills. Thanks to the business you received this certificate from, now you can enjoy exciting Las Vegas, NV too!</p>

  <div class="features-tab">FEATURES:</div>
  <div class="features-box">
    <ul class="features-list">
      <li><svg width="15" height="14" viewBox="0 0 15 14" fill="var(--red)"><rect x="0" y="6" width="3.5" height="8"/><path d="M5 6 L8.5 0.5 Q10.5 0.5 10 3.5 L9.5 5.5 H13.5 Q15 5.5 14.5 7.5 L13 13 Q12.6 14 11.5 14 H5 Z"/></svg>Travel 7 Days A Week</li>
      <li><svg width="15" height="14" viewBox="0 0 15 14" fill="var(--red)"><rect x="0" y="6" width="3.5" height="8"/><path d="M5 6 L8.5 0.5 Q10.5 0.5 10 3.5 L9.5 5.5 H13.5 Q15 5.5 14.5 7.5 L13 13 Q12.6 14 11.5 14 H5 Z"/></svg>Stay Your Choice Of Nights (1-4 Nights)</li>
      <li><svg width="15" height="14" viewBox="0 0 15 14" fill="var(--red)"><rect x="0" y="6" width="3.5" height="8"/><path d="M5 6 L8.5 0.5 Q10.5 0.5 10 3.5 L9.5 5.5 H13.5 Q15 5.5 14.5 7.5 L13 13 Q12.6 14 11.5 14 H5 Z"/></svg>Good For Two Adults &amp; Two Children</li>
      <li><svg width="15" height="14" viewBox="0 0 15 14" fill="var(--red)"><rect x="0" y="6" width="3.5" height="8"/><path d="M5 6 L8.5 0.5 Q10.5 0.5 10 3.5 L9.5 5.5 H13.5 Q15 5.5 14.5 7.5 L13 13 Q12.6 14 11.5 14 H5 Z"/></svg>Pay Just The Taxes &amp; Fees</li>
      <li><svg width="15" height="14" viewBox="0 0 15 14" fill="var(--red)"><rect x="0" y="6" width="3.5" height="8"/><path d="M5 6 L8.5 0.5 Q10.5 0.5 10 3.5 L9.5 5.5 H13.5 Q15 5.5 14.5 7.5 L13 13 Q12.6 14 11.5 14 H5 Z"/></svg>Multiple Travel Date Requests Allowed</li>
      <li><svg width="15" height="14" viewBox="0 0 15 14" fill="var(--red)"><rect x="0" y="6" width="3.5" height="8"/><path d="M5 6 L8.5 0.5 Q10.5 0.5 10 3.5 L9.5 5.5 H13.5 Q15 5.5 14.5 7.5 L13 13 Q12.6 14 11.5 14 H5 Z"/></svg>Fully Transferable To Another Person</li>
      <li><svg width="15" height="14" viewBox="0 0 15 14" fill="var(--red)"><rect x="0" y="6" width="3.5" height="8"/><path d="M5 6 L8.5 0.5 Q10.5 0.5 10 3.5 L9.5 5.5 H13.5 Q15 5.5 14.5 7.5 L13 13 Q12.6 14 11.5 14 H5 Z"/></svg>Just A 30 Days Advance Notice Required</li>
      <li><svg width="15" height="14" viewBox="0 0 15 14" fill="var(--red)"><rect x="0" y="6" width="3.5" height="8"/><path d="M5 6 L8.5 0.5 Q10.5 0.5 10 3.5 L9.5 5.5 H13.5 Q15 5.5 14.5 7.5 L13 13 Q12.6 14 11.5 14 H5 Z"/></svg>You Will Have 12 Months To Complete<br>Travel After Redemption</li>
    </ul>
  </div>

  <h2 class="how-title">HOW CAN WE DO THIS?</h2>

  <p class="how-item contract">
    <svg width="24" height="26" viewBox="0 0 24 26" fill="none" stroke="var(--yellow)" stroke-width="1.4"><rect x="1" y="1" width="16" height="22"/><path d="M4 6 H14 M4 10 H14 M4 14 H10"/><circle cx="6" cy="19" r="2.5"/><path d="M22 6 L13 20 L12 23 L14.5 21 L23 8 Z"/></svg>
    We contract with the world leading hotel chains and resorts to help them fill their otherwise empty rooms.
  </p>
  <p class="how-item revenue">
    <svg width="26" height="26" viewBox="0 0 26 26" fill="none" stroke="var(--yellow)" stroke-width="1.4"><path d="M2 12 L13 3 L24 12"/><path d="M4 12 V24 H22 V12"/><circle cx="19" cy="6" r="3.5"/><path d="M17.5 6 L18.7 7.2 L20.7 5"/><rect x="6" y="16" width="14" height="4"/><path d="M8 16 V14 H12 V16"/></svg>
    We help fill empty rooms which the hotels, resorts and cruise lines turn into additional revenue from other areas of their property and future bookings.
  </p>
  <p class="how-item occupancy">
    <svg width="26" height="26" viewBox="0 0 26 26" fill="none" stroke="var(--yellow)" stroke-width="1.4"><path d="M2 12 L13 3 L24 12"/><path d="M4 12 V24 H22 V12"/><circle cx="19" cy="6" r="3.5"/><path d="M17.5 6 L18.7 7.2 L20.7 5"/><rect x="6" y="16" width="14" height="4"/><path d="M8 16 V14 H12 V16"/></svg>
    Hotels rarely experience full occupancy, yet they remain open, providing rooms and services at fixed costs. So when hotels give out their rooms by partnering with marketing companies like us, they might miss out on the room fee, but they already didn't have that in the first place, at least now they have the opportunity to gain a customer for their in-house restaurants, room service, their casinos, an extra day stay, future bookings, etc.
  </p>

  <div class="divider"></div>
  <p class="certificate-meta">
    Certificate ID # 47261-38157<br>
    Expires 02/29/2020<br>
    *terms and conditions apply see website for details
  </p>

  <footer class="redeem-footer">VIEW ALL THE DETAILS OF THIS SPECIAL OFFER AND REDEEM ONLINE AT WWW.QOTAVERNIX.COM</footer>
</main>
</body>
</html>
```